Looking for a modern, Professional business card design

We have a simple business card, but are looking for a more modern, professional look. A sample of the basic card is attached as well as the logo. We would also like to add that we offer:
Struggling with your finances?
- Learn to become debt free
- Discover the power of cash
- Control your money instead of it controlling you
Let us help you achieve a new level of financial freedom!
Also, we would like to have a "SPECIAL OFFER!: FREE 30 minute consultation"
Financial Planning

```html
<!DOCTYPE html>
<html lang="en">
<head>
<meta charset="utf-8">
<title>Clearpath Money Coaching – Business Card</title>
<link rel="stylesheet" href="https://fonts.googleapis.com/css2?family=Arimo:wght@400;700&display=swap">
<style>
  :root {
    --backdrop: #4a413b;
    --card: #1c1c1d;
    --green: #3fae49;
    --white: #f2f2f2;
    --grey: #cfcfcf;
    --divider: #8a8a8a;
  }
  * { box-sizing: border-box; margin: 0; padding: 0; }
  html, body { width: 1200px; height: 787px; overflow: hidden; }
  body {
    background: var(--backdrop);
    font-family: "Arimo", Arial, sans-serif;
    display: flex;
    align-items: center;
    justify-content: center;
    gap: 40px;
  }
  .card {
    width: 540px;
    height: 309px;
    background: var(--card);
    border-radius: 4px;
    box-shadow: 0 6px 18px rgba(0,0,0,.35);
    color: var(--white);
    position: relative;
  }
  .brand {
    display: flex;
    align-items: center;
    gap: 10px;
  }
  .brand-dot {
    width: 26px; height: 26px;
    border-radius: 50%;
    background: var(--green);
    flex: none;
  }
  .brand-name {
    font-weight: 700;
    font-size: 26px;
    line-height: 1.05;
    color: var(--white);
  }

  /* Front */
  .card-front {
    padding: 30px 30px 0;
    text-align: center;
  }
  .card-front .brand { justify-content: center; margin-bottom: 26px; }
  .offer-heading {
    color: var(--green);
    font-weight: 700;
    font-size: 17px;
    letter-spacing: .3px;
    margin-bottom: 8px;
  }
  .offer-points {
    font-size: 14px;
    line-height: 1.45;
    color: var(--grey);
  }
  .offer-points .sep { color: var(--green); margin: 0 4px; }
  .special-offer {
    margin-top: 16px;
    font-size: 17px;
    font-weight: 700;
    color: var(--white);
  }

  /* Back */
  .card-back {
    display: flex;
    align-items: center;
    padding: 0 30px;
  }
  .card-back .brand { width: 205px; }
  .card-back .brand-name { font-size: 24px; }
  .divider {
    width: 1px;
    height: 130px;
    background: var(--divider);
    margin: 0 22px 0 14px;
  }
  .contact-name {
    color: var(--green);
    font-size: 21px;
    letter-spacing: .5px;
  }
  .contact-role {
    font-size: 16px;
    color: var(--white);
    margin: 3px 0 12px;
  }
  .contact-list { list-style: none; }
  .contact-list li {
    display: flex;
    align-items: center;
    gap: 9px;
    font-size: 15px;
    line-height: 1.55;
    color: var(--white);
  }
  .contact-list svg { width: 14px; height: 14px; flex: none; }
</style>
</head>
<body>

  <section class="card card-front">
    <div class="brand">
      <span class="brand-dot"></span>
      <span class="brand-name">Clearpath Money Coaching</span>
    </div>
    <h2 class="offer-heading">STRUGGLING WITH YOUR FINANCES?</h2>
    <p class="offer-points">
      Learn to become debt free <span class="sep">•</span> Discover the power of cash<br>
      Control your money instead of it controlling you<br>
      Let us help you achieve a new level of financial freedom!
    </p>
    <p class="special-offer">SPECIAL OFFER!: FREE 30 minute consultation</p>
  </section>

  <section class="card card-back">
    <div class="brand">
      <span class="brand-dot"></span>
      <span class="brand-name">Clearpath Money Coaching</span>
    </div>
    <div class="divider"></div>
    <div class="contact">
      <p class="contact-name">Daniel R. Hayes</p>
      <p class="contact-role">Personal Financial Coach</p>
      <ul class="contact-list">
        <li>
          <svg viewBox="0 0 14 14" aria-hidden="true"><rect x="3" y="0.5" width="8" height="13" rx="1.5" fill="none" stroke="#3fae49" stroke-width="1.4"/><circle cx="7" cy="11" r="0.9" fill="#3fae49"/></svg>
          (205) 555-0187
        </li>
        <li>
          <svg viewBox="0 0 14 14" aria-hidden="true"><rect x="0.5" y="2.5" width="13" height="9" fill="#3fae49"/><path d="M0.5 2.5 L7 8 L13.5 2.5" fill="none" stroke="#1c1c1d" stroke-width="1.2"/></svg>
          daniel@clearpathmoneycoach.com
        </li>
        <li>
          <svg viewBox="0 0 14 14" aria-hidden="true"><circle cx="7" cy="7" r="6.5" fill="#3fae49"/><path d="M1 7 H13 M7 0.5 C4 4 4 10 7 13.5 M7 0.5 C10 4 10 10 7 13.5" fill="none" stroke="#1c1c1d" stroke-width="1"/></svg>
          www.clearpathmoneycoach.com
        </li>
      </ul>
    </div>
  </section>

</body>
</html>
```